Redesign business cards

We have a new logo and I am not that happy with the layout of our existing card and looking for a change. Font is a bit small and the green can be hard to read. Logo may need a tidy up as the copy I have is not that hi-res too so require you to produce a hi-res version of the logo for us too. There will be three individual business cards to produce with just the names and phone numbers being different. Address will change too, but use what you see on the card for now.

Industry/Entity Type

Business

Requirements
Nice to have
• You could consider a redesign to the new logo, just not too radical. We like the blue and green hexagons as we feel that they are representative of oil industry that we are in.

```html
<!DOCTYPE html>
<html lang="en">
<head>
<meta charset="utf-8">
<title>Greenmere Oil Services – Business Cards</title>
<link rel="stylesheet" href="https://fonts.googleapis.com/css2?family=Open+Sans:wght@400;600;700&display=swap">
<style>
  :root {
    --backdrop: #a9adb4;
    --card-white: #f7f7f7;
    --card-shade: #e4e4e4;
    --brand-green: #8cc63f;
    --brand-orange: #f7941d;
    --swoosh-grey: #6d6e71;
    --ink-grey: #4d4d4f;
    --ink-white: #ffffff;
  }
  * { margin: 0; padding: 0; box-sizing: border-box; }
  html, body {
    width: 1200px; height: 866px; overflow: hidden;
    background: var(--backdrop);
    font-family: "Open Sans", Arial, sans-serif;
  }
  .stage { position: relative; width: 1200px; height: 866px; }

  .card {
    position: absolute;
    width: 520px; height: 300px;
    background: radial-gradient(ellipse at 45% 45%, var(--card-white) 0%, var(--card-shade) 100%);
    box-shadow: 0 10px 24px rgba(0,0,0,0.25);
    overflow: hidden;
  }
  .card--front { left: 70px; top: 110px; }
  .card--back  { left: 610px; top: 450px; }

  .brand {
    position: absolute;
    display: flex; align-items: center; gap: 12px;
  }
  .brand__mark {
    flex: none;
    width: 30px; height: 30px;
    background: var(--brand-orange);
  }
  .brand__name {
    font-weight: 700;
    color: var(--brand-green);
    line-height: 1.05;
    white-space: nowrap;
  }
  .card--front .brand { left: 50%; top: 50%; transform: translate(-50%, -50%); }
  .card--front .brand__name { font-size: 34px; }
  .card--front .brand__mark { width: 40px; height: 40px; }

  .card--back .brand { left: 28px; top: 58px; }
  .card--back .brand__name { font-size: 24px; }

  .swoosh { position: absolute; inset: 0; width: 100%; height: 100%; }

  .holder { position: absolute; left: 28px; top: 140px; }
  .holder__name { font-size: 16px; font-weight: 700; color: var(--brand-green); }
  .holder__role { font-size: 15px; font-weight: 400; color: var(--ink-grey); margin-top: 2px; }

  .contact {
    position: absolute; right: 16px; top: 72px;
    list-style: none; text-align: right;
    color: var(--ink-white); font-size: 12px; line-height: 1.6;
  }
  .contact li { display: flex; justify-content: flex-end; align-items: center; gap: 5px; white-space: nowrap; }
  .contact svg { width: 11px; height: 11px; fill: var(--ink-white); }
</style>
</head>
<body>
<main class="stage">

  <section class="card card--front" aria-label="Business card front">
    <div class="brand">
      <span class="brand__mark"></span>
      <span class="brand__name">Greenmere<br>Oil Services</span>
    </div>
  </section>

  <section class="card card--back" aria-label="Business card back">
    <svg class="swoosh" viewBox="0 0 520 300" preserveAspectRatio="none" aria-hidden="true">
      <path fill="var(--swoosh-grey)" d="M345,8 C318,85 315,170 270,205 C210,250 110,252 0,238 L0,222 C110,236 200,232 255,195 C300,160 310,80 345,8 Z"/>
      <path fill="var(--swoosh-grey)" d="M352,6 C330,90 318,150 280,180 C240,205 205,210 180,212 C220,205 255,190 275,168 C305,132 325,70 352,6 Z"/>
      <path fill="var(--brand-green)" d="M362,0 L520,0 L520,300 L0,300 L0,262 C120,276 240,270 300,215 C332,182 338,80 362,0 Z"/>
    </svg>

    <div class="brand">
      <span class="brand__mark"></span>
      <span class="brand__name">Greenmere<br>Oil Services</span>
    </div>

    <div class="holder">
      <p class="holder__name">Maren Callow-Hart</p>
      <p class="holder__role">Consultant</p>
    </div>

    <ul class="contact">
      <li>41.9th floor,Harbour</li>
      <li>Point Road NTW</li>
      <li>014 220 7310
        <svg viewBox="0 0 24 24" aria-hidden="true"><path d="M6.6 10.8a15.1 15.1 0 0 0 6.6 6.6l2.2-2.2a1 1 0 0 1 1-.25 11.4 11.4 0 0 0 3.6.57 1 1 0 0 1 1 1V20a1 1 0 0 1-1 1A17 17 0 0 1 3 4a1 1 0 0 1 1-1h3.5a1 1 0 0 1 1 1c0 1.25.2 2.45.57 3.6a1 1 0 0 1-.25 1z"/></svg>
      </li>
      <li>014 220 7311
        <svg viewBox="0 0 24 24" aria-hidden="true"><path d="M6 2h10v5H6zM4 8h16a2 2 0 0 1 2 2v8H2v-8a2 2 0 0 1 2-2zm3 5h4v2H7zm7 0h3v2h-3zM6 19h12v3H6z"/></svg>
      </li>
      <li>hello@greenmere.com
        <svg viewBox="0 0 24 24" aria-hidden="true"><path d="M2 5h20v14H2zm2 2v.5l8 5 8-5V7l-8 5z"/></svg>
      </li>
      <li>www.greenmereoil.com</li>
    </ul>
  </section>

</main>
</body>
</html>
```